Business Card: RW Office Partners - Your organised problem solver

Business Name: RW Office Partners
Website: www.rwofficepartners.com.au
Email: marisol@rwofficepartners.com.au
Mobile: 61 482 907 236
Facebook: @rwofficepartners
Instrgram: @rwofficepartners

Brading Colours:
HEX
#986474
#ddccd3
#7a8498
#c9d8e4
#000000
#ffffff

Tag Line: Your organised problem solver

Link to DRAFT website:
https://deskhelpcollective.wixsite.com/rw-office-partners

About Page from the website:
My name is Marisol Wrenfield, and I would love to assist you to become more productive in your day to day and achieve your business and personal goals.
My mission is to give you time, time to work on the important tasks of your business or to be able to spend more time with your family. I will take on the tasks you don’t have time for, don’t know well or simply don’t like to do.
I have an extensive background in Administration, Tender Coordination, Document Control, WHS and Quality Management working primarily in the Construction, Mining and Corporate World.
I am passionate about being organised, having order and making things in your life (and mine) easier! I love to watch something unfold and grow into something amazing! I am known for being the go-to problem solver, the organiser of all things, producing high standards of work even under pressure. I’m also a confident communicator, and I understand that you’re busy running your business.

Target Market(s)

Small to Medium Business who require assistance in their business by a virtual assistant.

Industry/Entity Type

Virtual Assistant

Contact Information for Business Card

Mobile: 61 482 907 236

Font styles to use
Sans Serif

Colors
ffffff

Requirements
Must have
• Branding Colours as outlined.
Contact Details as outlined.
Logo as provided.
Proper contact details - mobile, facebook, instragm, website.
Simple, Elegant, very clean looking.
Should not have
• Note cute with pictures.
Not too girly as still want to market to construction companies.

```html
<!DOCTYPE html>
<html lang="en">
<head>
<meta charset="utf-8">
<title>RW Office Partners – Business Card</title>
<link rel="stylesheet" href="https://fonts.googleapis.com/css2?family=Montserrat:wght@600&family=Roboto:wght@400;500&display=swap">
<style>
  :root {
    --mauve: #8a5d6e;
    --slate: #7a8498;
    --paper: #ffffff;
    --ink: #3b3b3b;
    --backdrop: #6a6768;
    --white-text: #ffffff;
  }
  * { margin: 0; padding: 0; box-sizing: border-box; }
  html, body { width: 1200px; height: 1200px; overflow: hidden; }
  body {
    background: var(--backdrop);
    position: relative;
    font-family: "Roboto", Arial, sans-serif;
  }
  .card {
    position: absolute;
    width: 712px;
    height: 416px;
    border-radius: 28px;
    overflow: hidden;
    background: var(--paper);
  }
  .card--front { left: 238px; top: 120px; }
  .card--back  { left: 231px; top: 645px; }

  /* Front */
  .front-wordmark {
    position: absolute;
    left: 0; right: 0; top: 132px;
    text-align: center;
    font-family: "Montserrat", Arial, sans-serif;
    font-weight: 600;
    font-size: 58px;
    letter-spacing: 1px;
    color: var(--mauve);
  }
  .front-social {
    position: absolute;
    left: 0; right: 0; top: 350px;
    display: flex; justify-content: center; gap: 12px;
    font-size: 18px; color: var(--ink);
  }
  .social-item { display: flex; align-items: center; gap: 10px; }
  .social-mark {
    width: 15px; height: 15px; border-radius: 3px;
    background: var(--mauve); display: inline-block;
  }
  .front-band {
    position: absolute; left: 0; right: 0; bottom: 0; height: 17px;
    display: flex;
  }
  .front-band__mauve { width: 357px; background: var(--mauve); }
  .front-band__slate { flex: 1; background: var(--slate); }

  /* Back */
  .back-shapes { position: absolute; inset: 0; }
  .back-wordmark {
    position: absolute; left: 30px; top: 130px; width: 220px;
    font-family: "Montserrat", Arial, sans-serif;
    font-weight: 600; font-size: 40px; line-height: 1.12;
    color: var(--mauve);
  }
  .contact-name {
    position: absolute; left: 349px; top: 85px;
    font-family: "Montserrat", Arial, sans-serif;
    font-weight: 600; font-size: 25px; color: var(--white-text);
  }
  .contact-role {
    position: absolute; left: 349px; top: 118px;
    font-size: 18px; color: var(--white-text);
  }
  .contact-list {
    position: absolute; left: 349px; top: 162px;
    list-style: none; color: var(--white-text); font-size: 18.5px;
  }
  .contact-list li {
    display: flex; align-items: center; gap: 12px; height: 26.3px;
  }
  .contact-icon { width: 17px; height: 17px; flex: none; }
  .contact-icon--plain {
    width: 15px; height: 15px; border-radius: 3px;
    background: var(--white-text); margin: 0 1px;
  }
  .tagline {
    position: absolute; left: 349px; top: 346px;
    font-size: 18px; color: var(--white-text);
  }
</style>
</head>
<body>

<section class="card card--front" aria-label="Business card front">
  <div class="front-wordmark">RW Office Partners</div>
  <div class="front-social">
    <span class="social-item"><span class="social-mark"></span>@rwofficepartners</span>
    <span class="social-item"><span class="social-mark"></span>@rwofficepartners</span>
  </div>
  <div class="front-band">
    <div class="front-band__mauve"></div>
    <div class="front-band__slate"></div>
  </div>
</section>

<section class="card card--back" aria-label="Business card back">
  <svg class="back-shapes" width="712" height="416" viewBox="0 0 712 416">
    <rect width="712" height="416" fill="var(--mauve)"/>
    <rect x="0" y="343" width="712" height="35" fill="var(--slate)"/>
    <path d="M0 0 H252 C305 110 315 280 268 416 H0 Z" fill="var(--slate)"/>
    <path d="M0 0 H248 C298 110 304 280 252 416 H0 Z" fill="var(--paper)"/>
  </svg>

  <div class="back-wordmark">RW Office Partners</div>

  <div class="contact-name">Marisol Wrenfield</div>
  <div class="contact-role">Virtual Assistant</div>

  <ul class="contact-list">
    <li>
      <svg class="contact-icon" viewBox="0 0 24 24" aria-hidden="true"><path fill="#fff" d="M3 8c0-3 4-5 9-5s9 2 9 5v2h-5V8c-1-.6-2.5-1-4-1s-3 .4-4 1v2H3z M6 12h12l2 8H4z"/></svg>
      61 482 907 236
    </li>
    <li>
      <svg class="contact-icon" viewBox="0 0 24 24" aria-hidden="true"><rect x="2" y="5" width="20" height="14" fill="none" stroke="#fff" stroke-width="2"/><path d="M2 5l10 8 10-8" fill="none" stroke="#fff" stroke-width="2"/></svg>
      marisol@rwofficepartners.com.au
    </li>
    <li>
      <svg class="contact-icon" viewBox="0 0 24 24" aria-hidden="true"><g fill="none" stroke="#fff" stroke-width="1.6"><circle cx="12" cy="12" r="9"/><ellipse cx="12" cy="12" rx="4" ry="9"/><path d="M3 12h18M5 7h14M5 17h14"/></g></svg>
      www.rwofficepartners.com.au
    </li>
    <li><span class="contact-icon contact-icon--plain"></span>@rwofficepartners</li>
    <li><span class="contact-icon contact-icon--plain"></span>@rwofficepartners</li>
  </ul>

  <div class="tagline">Your organised problem solver</div>
</section>

</body>
</html>
```